Flyer-Design für Hundephysiopraxis
Zielgruppe
Ich bin selbstständige Hundephysiotherapeutin / Hundeosteopathin /Hundefitnesstrainerin. Meine Zielgruppe sind Hundehalter bzw. allgemein Tierhalter (biete noch weitere Dinge für Hunde/Tiere an) aber auch Tierärzte.
Aufgabenstellung
Es wäre schön, wenn Sie die Texte ähnlich wie auf meiner Homepage gestalten (z.B. Infos aus der Startseite oder Therapieformen).
Prinzipiell sollte es eher natürlich, freundlich und nett gestaltet sein. Schlichtere Farben passend zum Logo.
Homepage: www.pfotenruhe-mitte.de
Bei den Maßen bin ich offen, hatte aber eher an diesen 'typischen Flyer' gedacht (3 seitiger Flyer mit Vorder und Rückseite) bin aber prinzipiell offen :)
Einen Beispiel Flyer habe ich drangehängt sowie z.B. schon ein paar Fotos die man ggf nutzen kann. Weitere Behandlunsfotos kann ich gerne nachreichen.
Die Flyer sollen hauptsächlich bei z.B. Tierärzten / Tierklinik / Tiernahrungsmärkte wie Kornbeutel ausgelegt werden damit Menschen die mich noch nicht kennen auf meine Arbeit aufmerksam werden.

```html
<!DOCTYPE html>
<html lang="de">
<head>
<meta charset="utf-8">
<title>Hundephysiotherapie & Hundeosteopathie – Flyer</title>
<link href="https://fonts.googleapis.com/css2?family=Open+Sans:wght@400;800&family=Source+Sans+3:wght@300;400;600&display=swap" rel="stylesheet">
<style>
  :root{
    --orange:#f5a062;
    --cream:#fbe7da;
    --brown:#8e5a3a;
    --white:#ffffff;
    --photo-green:#7fb04a;
    --photo-light:#e9e2d8;
  }
  *{margin:0;padding:0;box-sizing:border-box}
  html,body{width:1200px;height:810px;overflow:hidden;background:var(--orange)}
  .flyer{position:relative;width:1200px;height:810px;background:var(--orange);color:var(--white);font-family:"Source Sans 3",sans-serif;overflow:hidden}
  .backdrop{position:absolute;inset:0}
  .intro{position:absolute;left:0;top:18px;width:375px;text-align:center}
  .intro__title{font-family:"Open Sans",sans-serif;font-weight:800;font-size:27px;line-height:30px;letter-spacing:1.6px}
  .intro__text{font-family:"Open Sans",sans-serif;font-size:10.3px;line-height:12.05px;letter-spacing:.45px;margin-top:20px;padding:0 8px}
  .intro__text + .intro__text{margin-top:12px}
  .hero-photo{position:absolute;left:0;top:380px;width:410px;height:430px;background:linear-gradient(160deg,rgba(255,255,255,.55) 0%,rgba(229,160,110,.6) 45%,rgba(142,90,58,.5) 100%);border-radius:0 60% 0 0}
  .section{position:absolute}
  .section__heading{font-weight:400;font-size:17px;line-height:19px}
  .list{list-style:none;font-size:11px;line-height:13.4px}
  .list li::before{content:"• "}
  .list--semi{font-weight:600}
  .list--light{font-weight:300}
  .note{font-weight:300;font-size:11px;line-height:13.4px}
  .body{font-weight:600;font-size:11px;line-height:13.4px}
  .photo{position:absolute;background:linear-gradient(180deg,var(--photo-green),#5f8f33)}
  .photo--round{border-radius:50%}
  .photo--treat{left:664px;top:85px;width:226px;height:226px}
  .photo--balance{left:672px;top:331px;width:191px;height:190px;border-radius:36px}
  .photo--indoor{left:660px;top:540px;width:226px;height:226px;background:linear-gradient(180deg,#c9ad8c,var(--photo-light))}
  .footer{position:absolute;left:824px;top:795px;font-family:"Open Sans",sans-serif;font-size:7.5px;letter-spacing:.4px;color:rgba(255,255,255,.75)}
</style>
</head>
<body>
<div class="flyer">
  <svg class="backdrop" width="1200" height="810" viewBox="0 0 1200 810" aria-hidden="true">
    <path d="M762,0 C775,60 830,80 900,55 C980,28 1050,20 1100,60 C1150,95 1175,115 1200,125 L1200,0 Z" fill="var(--cream)"/>
    <path d="M0,595 C60,590 120,650 180,690 C260,735 380,700 450,740 C490,765 505,790 510,810 L0,810 Z" fill="var(--brown)"/>
  </svg>

  <div class="hero-photo" role="img" aria-label="Freigestellter Beagle, aufgerichtet auf den Hinterbeinen, mit großen weißen Pfotenabdrücken"></div>

  <section class="intro">
    <h1 class="intro__title">Hundephysiotherapie<br>&amp; Hundeosteopathie (i.A.)</h1>
    <p class="intro__text">In der Humanmedizin wird die Physiotherapie bei der Genesung der Patienten schon selbstverständlich und unterstützend eingesetzt. Tiere können an ähnlichen Problemen leiden wie wir Menschen. Sie haben genau so Schmerzen und dies schränkt ihr Leben oftmals ein. Wir können unsere Schmerzen äußern. Viele Hunde jedoch leben mit diesem Schmerz viele Wochen, ehe es unerträglich wird und sie lahmen oder andere Dinge anzeigen. Gerade deshalb ist die Physiotherapie so enorm wichtig, damit unsere Hunde unbeschwert und ohne Schmerzen lange an unserer Seite bleiben.</p>
    <p class="intro__text">Jeder Körper ist ein individuelles und komplexes System mit eigenen Anforderungen an Beanspruchungen, Intensitäten und Erholungsphasen. Entsprechend umfangreich aufgestellt ist das Therapiespektrum meiner Arbeit. Dabei immer im Fokus: Die stets vollkommen individuellen Therapieprogramme, in enger Zusammenarbeit mit dem Tierarzt. Sensibel abgestimmt auf die spezifischen Anforderungen der einzelnen Krankheitsbilder. Jeder Hund hat eine andere Hintergrundgeschichte und auch dies berücksichtige ich bei meinen Therapien. Mein Ziel ist es, die Lebensfreude und Lebensqualität unserer Vierbeiner zu erhalten oder gar zu verbessern.</p>
  </section>

  <section class="section" style="left:387px;top:20px">
    <h2 class="section__heading">Einsatzmöglichkeiten der Physiotheraphie:</h2>
    <ul class="list list--semi" style="margin-top:15px;margin-left:2px">
      <li>Schmerzlinderung</li><li>Muskelaufbau</li><li>Koordinationsschulung</li><li>Konditionsaufbau</li>
      <li>Verbesserung der Beweglichkeit (Sehnen, Bänder und Gelenke)</li><li>Lösen von Blockaden</li>
      <li>Prävention</li><li>Gangschulung</li><li>Nachsorge nach Operationen</li><li>Wundheilungsstörungen</li>
      <li>Muskelverspannungen</li><li>neurologische Erkrankungen</li><li>degenerative Erkrankungen</li>
    </ul>
  </section>

  <section class="section" style="left:386px;top:262px">
    <h2 class="section__heading">Hundephysiotheraphie<br>Therapieformen:</h2>
    <ul class="list list--light" style="margin-top:15px">
      <li>herapeutische Massage</li><li>manuelle Therapie</li><li>passives Bewegen</li><li>aktives Bewegen</li>
      <li>passive Dehnungen</li><li>aktive Dehnungen</li><li>Gelenkmobilisation</li><li>Kältetherapie</li>
      <li>Wärmetherapie</li><li>Narbenbehandlung</li><li>Kinesio Taping / Vet taping</li><li>Behandlung mit Vibrasonic</li><li>u.v.m.</li>
    </ul>
    <p class="note" style="margin-top:14px;width:280px">Dazu biete ich weiterhin eine Magnetfeldtherapie an.<br>&nbsp;Diese unterstützt bei Verspannungen, aktuen Verletzungen, Schmerzen u.v.m.</p>
  </section>

  <section class="section" style="left:413px;top:572px;width:245px">
    <h2 class="section__heading">Wirkung:</h2>
    <ul class="list list--light" style="margin-top:8px">
      <li>Aktivierung von Stoffwechsel und Durchblutung</li><li>Schmerzlinderung</li><li>keimabtötend</li>
      <li>Stimulierung der Angioneogenese (Neubildung von Zellen und Gewebe)</li>
    </ul>
  </section>

  <div class="photo photo--round photo--treat" role="img" aria-label="Therapeutin behandelt einen liegenden Spaniel auf der Wiese"></div>
  <div class="photo photo--balance" role="img" aria-label="Hund steht auf lila Balancepads im Garten"></div>
  <div class="photo photo--round photo--indoor" role="img" aria-label="Therapeutin massiert einen liegenden Hund auf einer Behandlungsdecke"></div>

  <section class="section" style="left:904px;top:78px;width:290px">
    <h2 class="section__heading">Hundeosteopathie</h2>
    <p class="body" style="margin-top:14px">• Aktuell befinde ich mich in der Ausbildung zur Hundeosteopathin.<br>• Natürlich werde ich schon jetzt einige gelernte Anwendungen in meiner Behandlung miteinfließen lassen.</p>
    <p class="body" style="margin-top:13px">• Prüfung voraussichtlich im Mai 2023</p>
    <p class="body" style="margin-top:27px">Für mich steht Dein Hund an erster Stelle! Ich habe selbst Erfahrungen mit Tierschutzhunden, sowie Hunden aus deutscher Zucht und weiß, dass manche Hunde "ihr Päckchen" zu tragen haben. Umso mehr möchte ich, dass sich Dein Vierbeiner bei mir wohlfühlt, er mir Vertrauen schenkt und gerne zur Physiotherapie geht.</p>
  </section>

  <section class="section" style="left:904px;top:332px;width:296px">
    <h2 class="section__heading">Dorn Therapie und&nbsp; Breuß Massage</h2>
    <p class="body" style="margin-top:14px">• Ergänzend zur Physiotheraphie<br>• Breuz-Massage:<br>Bei der Breuß-Massage wird die Wirbelsäule durch eine wohltuende Massage am Kreuzbein entspannt und gestreckt. Durch gezielte Griffe und Dehnungen wird der Rücken gelockert und verschobene Wirbel schmerzfrei in die ursprüngliche Position gebracht.</p>
    <p class="body" style="margin-top:13px">• Dorn-Theraphie:<br>Die Wirbelsäulentherapie nach Dorn, ist eine sanfte Methode, die zur Behandlung von Beschwerden des Bewegungsapparates zum Einsatz kommt. Der Therapeut bringt in der Therapiesitzung Wirbel und Gelenke mit sanften und einfühlsamen Bewegungen in ihre richtige Position zurück.</p>
  </section>

  <section class="section" style="left:904px;top:574px;width:296px">
    <h2 class="section__heading">Hundefitnesstrainer (i.A.)</h2>
    <p class="body" style="margin-top:14px">•&nbsp; Perfekte Ergänzung nach erfolgreicher Hundephysiotherapie</p>
    <p class="body" style="margin-top:13px">•&nbsp; individuelle Trainingspläne<br>•&nbsp; Muskelaufbautraining<br>•&nbsp; Beweglichkeitstraining<br>•&nbsp; Abnehmtraining<br>•&nbsp; Fitnesstraining<br>•&nbsp; Gehirntraining<br>•&nbsp; Schult den optimalen Bewegungsablauf<br>•&nbsp; Tipps und Training für Sporthunde<br>•&nbsp; z.B. mit Cavaletti oder Balancepads</p>
  </section>

  <p class="footer">Lena Marwitz, Birkenweg 7, 35100 Talheim</p>
</div>
</body>
</html>
```